Interior Plaster, Plasterboard Fixing & Installation Business CardDesign

BRANVO The name was formed by me, in talking to my accountant, whilst skim coating his walls and I had seen an imperfection in a wall that needed to be skim coated to deflect the light from the imperfection. I responded to him saying...."just Bran Vo". The idea originates from the process of applying a skim coat of interior plaster to a wall to achieve a smoother surface. This is required prior to many applications, applying wall paper, preparation for paint, after removing wall paper, improving aesthetics, joints that have not been properly jointed etc. Different types of light reflected on the surface, makes poor jointing more visible. In addition, the businesses key functions will be interior plastering, plaster board installation (ceilings and walls) and plasterboard jointing to a level that is prepared for a painter. Once the plaster is applied the surface requires sanding using different types of sanding equipment manual and electronic, including the use of specialised paint-on sealers for the surface. I believe the name is simple, easy to remember, but may be read incorrectly. I have had people ask if it was Bran Vo, referring to information technology.

For now, this entire concept is driven by passion and started 2 years ago whilst renovating my own home.

I need to be able to use your expertise to translate my ideas, starting with business card and progressing to a website incorporating anything and everything in between. The final design should be easy to understand, read and standout with an element of uniqueness. Humour maybe an option, or the idea of leaving a prospect with something that is thought provoking.
Updates

Hi All Ideas look fine so far, but would expect to see different colour options. I am thinking plaster thats cream in colour, so more earthy colour on the card. A picture of a trowel to replace the I in BRANVO maybe. I like the swirl that is created by a notched trowel moving through plaster. Perhaps a more modern or fresher look. With BRANVO, could you consider reversing the direction of the K for instance facing in the opposite direction. In saying this I look to you for your experience and expertise with the idea. The other option with the K, could be to remove the first straight line, i hope that my explanation helps. Sorry if it doesn't. Thanks heaps :)

Please include the type of service. Plasterboard Services

I have considered the idea of the K being reversed, and I am of the view that it presents a challenge reading and understanding. Moving forward I would however like to use the K in the normal direction but without the first straight line. I need to see more colour options that are grey or earthy. Can a picture of a trowel be included if it makes sense and with that tool being frequently used in plastering.

Industry/Entity Type

Business

Contact Information for Business Card

Company name: BranVo
Name: Dorian Pekke
Title: Director
Email address: pekkedp@mailvora.example
Mobile number: 0210 481 7092
Address: 17 Tamsin Lane, Glenfield, Auckland, 0629

```html
<!DOCTYPE html>
<html lang="en">
<head>
<meta charset="utf-8">
<title>BranVo Business Card</title>
<link rel="stylesheet" href="https://fonts.googleapis.com/css2?family=Exo+2:wght@400;500;700&family=Open+Sans:wght@400&display=swap">
<style>
  :root {
    --page-bg: #262628;
    --card-base: #3d3b3c;
    --pattern-light: #4a4644;
    --pattern-warm: #5a5247;
    --panel-dark: #302e2e;
    --brand-orange: #e8612a;
    --trowel-tone: #8a8178;
    --text-light: #f2f2f2;
    --text-muted: #cfc8bf;
    --rule-light: #e6e6e6;
  }
  html, body {
    margin: 0;
    width: 1200px;
    height: 816px;
    overflow: hidden;
    background: var(--page-bg);
  }
  .business-card {
    position: absolute;
    left: 75px;
    top: 108px;
    width: 1050px;
    height: 600px;
    border-radius: 48px;
    overflow: hidden;
    background: var(--card-base);
    font-family: "Exo 2", sans-serif;
  }
  .texture-field {
    position: absolute;
    inset: 0;
    background: linear-gradient(135deg, var(--pattern-light), var(--pattern-warm) 50%, var(--pattern-light));
  }
  .logo-tab {
    position: absolute;
    left: 170px;
    top: 0;
    width: 620px;
    height: 290px;
    background: var(--panel-dark);
    border-radius: 0 0 40px 40px;
  }
  .brand-row {
    position: absolute;
    left: 0;
    right: 0;
    top: 86px;
    display: flex;
    justify-content: center;
    align-items: center;
    gap: 22px;
  }
  .trowel-motif {
    width: 64px;
    height: 64px;
    border-radius: 8px;
    background: linear-gradient(135deg, var(--trowel-tone), var(--pattern-warm));
  }
  .brand-name {
    margin: 0;
    font-family: "Exo 2", sans-serif;
    font-weight: 700;
    font-size: 100px;
    line-height: 1;
    color: var(--brand-orange);
  }
  .service-line {
    position: absolute;
    left: 0;
    right: 0;
    top: 206px;
    margin: 0;
    text-align: center;
    font-size: 24px;
    font-weight: 500;
    letter-spacing: 3px;
    text-transform: uppercase;
    color: var(--text-muted);
  }
  .info-band {
    position: absolute;
    left: 0;
    right: 0;
    top: 300px;
    height: 150px;
    background: var(--panel-dark);
  }
  .person {
    position: absolute;
    right: 520px;
    top: 46px;
    text-align: right;
    color: var(--text-light);
  }
  .person-name {
    margin: 0;
    font-size: 34px;
    font-weight: 500;
    letter-spacing: 1px;
    line-height: 1.1;
  }
  .person-title {
    margin: 0;
    font-size: 21px;
    font-weight: 400;
    letter-spacing: 1px;
  }
  .divider {
    position: absolute;
    left: 550px;
    top: 12px;
    width: 2px;
    height: 126px;
    background: var(--rule-light);
  }
  .contact-list {
    position: absolute;
    left: 572px;
    top: 20px;
    margin: 0;
    padding: 0;
    list-style: none;
    font-family: "Open Sans", sans-serif;
    font-size: 17px;
    line-height: 36px;
    color: var(--text-light);
    white-space: nowrap;
  }
</style>
</head>
<body>
  <section class="business-card">
    <div class="texture-field" role="img" aria-label="Decorative hexagon honeycomb pattern in warm grey tones"></div>
    <div class="logo-tab">
      <div class="brand-row">
        <div class="trowel-motif" role="img" aria-label="Plastering trowel motif"></div>
        <h1 class="brand-name">BranVo</h1>
      </div>
      <p class="service-line">Plasterboard Services</p>
    </div>
    <div class="info-band">
      <div class="person">
        <p class="person-name">Dorian Pekke</p>
        <p class="person-title">Director</p>
      </div>
      <div class="divider"></div>
      <ul class="contact-list">
        <li>0210 481 7092</li>
        <li>pekkedp@mailvora.example</li>
        <li>17 Tamsin Lane, Glenfield, Auckland, 0629</li>
      </ul>
    </div>
  </section>
</body>
</html>
```